Personal training and nutrition business needs business card design

We need a business card that outlays our services and invites potential customers to join our team and take the first step to a healthier and more enjoyable life. We cater for any level of fitness and specialize in weight loss and conditioning, strength training, muscle gain and strength endurance. Whether you are just starting off or need some help getting to the next level of your journey we are here to get the job done.
We specialize in one on one or one on two personal training sessions and each program will be custom made to suit individual fitness goals of our clients

```html
<!DOCTYPE html>
<html lang="en">
<head>
<meta charset="utf-8">
<title>Pulse &amp; Forge – Business Card</title>
<link href="https://fonts.googleapis.com/css2?family=Bebas+Neue&family=Arimo:wght@400&family=Oswald:wght@500&display=swap" rel="stylesheet">
<style>
  :root {
    --backdrop: #535353;
    --card-white: #ffffff;
    --card-black: #000000;
    --ink: #111111;
    --purple-deep: #6a409e;
    --purple-mid: #85489f;
    --purple-light: #a65da8;
    --tagline: #b565b8;
  }
  * { margin: 0; padding: 0; box-sizing: border-box; }
  html, body {
    width: 1200px; height: 801px; overflow: hidden;
    background: var(--backdrop);
  }
  .stage { position: relative; width: 1200px; height: 801px; }

  .card {
    position: absolute; top: 274px;
    width: 443px; height: 263px; overflow: hidden;
  }
  .card--front { left: 153px; background: var(--card-white); }
  .card--back { left: 625px; background: var(--card-black); }

  .front-accent {
    position: absolute; right: -120px; top: 18px;
    width: 300px; height: 300px; border-radius: 50%;
    background: linear-gradient(90deg, var(--purple-deep), var(--purple-light));
  }

  .holder-name {
    position: absolute; left: 24px; top: 38px;
    font-family: "Bebas Neue", sans-serif; font-size: 25px; line-height: 1;
    color: var(--purple-mid); letter-spacing: 0.2px;
  }
  .holder-role, .address, .contact-list {
    font-family: "Arimo", sans-serif; font-size: 12.5px; color: var(--ink);
  }
  .holder-role { position: absolute; left: 23px; top: 62px; }
  .address { position: absolute; left: 23px; top: 104px; line-height: 15.6px; }
  .contact-list {
    position: absolute; left: 23px; top: 182px; list-style: none; line-height: 15.6px;
  }
  .contact-list li { display: flex; align-items: center; gap: 4px; }
  .contact-list svg { width: 12px; height: 12px; flex: none; }
  .web-highlight { color: var(--purple-mid); }

  .brand-lockup {
    position: absolute; left: 0; right: 0; top: 70px;
    display: flex; flex-direction: column; align-items: center;
  }
  .brand-square {
    width: 46px; height: 46px;
    background: var(--purple-mid);
  }
  .brand-name {
    margin-top: 22px;
    font-family: "Bebas Neue", sans-serif; font-size: 42px; line-height: 1;
    color: var(--card-white); letter-spacing: 1px;
  }
  .brand-tagline {
    margin-top: 6px;
    font-family: "Oswald", sans-serif; font-weight: 500; font-size: 7.5px;
    color: var(--tagline); letter-spacing: 0.9px;
  }
</style>
</head>
<body>
<main class="stage">
  <section class="card card--front" aria-label="Card front">
    <div class="front-accent"></div>
    <h1 class="holder-name">Dana Whitlow</h1>
    <p class="holder-role">Managing Director</p>
    <address class="address">88 Larkspur Avenue<br>Brookfield 30917<br>Eastmoor</address>
    <ul class="contact-list">
      <li>
        <svg viewBox="0 0 24 24" aria-hidden="true"><path fill="var(--purple-mid)" d="M6.6 10.8a15.1 15.1 0 0 0 6.6 6.6l2.2-2.2a1 1 0 0 1 1-.25 11.4 11.4 0 0 0 3.6.57 1 1 0 0 1 1 1V20a1 1 0 0 1-1 1A17 17 0 0 1 3 4a1 1 0 0 1 1-1h3.5a1 1 0 0 1 1 1c0 1.25.2 2.45.57 3.57a1 1 0 0 1-.25 1z"/></svg>
        055-204 318 672
      </li>
      <li>
        <svg viewBox="0 0 24 24" aria-hidden="true"><rect x="2" y="5" width="20" height="14" fill="var(--purple-mid)"/><path d="M2 5l10 8 10-8" fill="none" stroke="#fff" stroke-width="1.6"/></svg>
        hello@pulseforge.fit
      </li>
      <li>
        <svg viewBox="0 0 24 24" aria-hidden="true"><g fill="none" stroke="var(--purple-mid)" stroke-width="2"><circle cx="12" cy="12" r="9.5"/><ellipse cx="12" cy="12" rx="4" ry="9.5"/><path d="M2.5 12h19M4 7h16M4 17h16"/></g></svg>
        www.<span class="web-highlight">pulseforge</span>.fit
      </li>
    </ul>
  </section>

  <section class="card card--back" aria-label="Card back">
    <div class="brand-lockup">
      <div class="brand-square"></div>
      <p class="brand-name">Pulse &amp; Forge</p>
      <p class="brand-tagline">PERSONAL TRAINING.&nbsp; NUTRITION. MOTIVATION</p>
    </div>
  </section>
</main>
</body>
</html>
```